Business Card Design Project

I require a business card with the following information on them for various different people;
name
m:
f:
e:
I have a logo already and will attached that. We are in the construction industry. I require something clean and simple but eye catching at the same time. You can use another colour with our logo if you like and you can style the logo as well if you wish. I am open.
Also it needs to be front and back design.
Industry/Entity Type
Construction
Requirements
Must have
- Logo, name, mobile, fax and email address.
Front and back design

```html
<!DOCTYPE html>
<html lang="en">
<head>
<meta charset="utf-8">
<title>Orlenby Build Co – Business Card, Front and Back</title>
<link rel="stylesheet" href="https://fonts.googleapis.com/css2?family=Open+Sans:wght@400;600;700&display=swap">
<style>
  :root {
    --backdrop: #a97b22;
    --card-white: #ffffff;
    --brand-green: #62b22b;
    --brand-green-light: #c3e45f;
    --brand-green-mid: #a6d64d;
    --tab-green-dark: #4a8f1f;
    --tab-green-light: #8cc83e;
    --text-dark: #2b2b2b;
    --name-green: #6cb52d;
  }
  html, body {
    margin: 0;
    padding: 0;
    width: 1200px;
    height: 686px;
    overflow: hidden;
    background: var(--backdrop);
    font-family: "Open Sans", Arial, sans-serif;
  }
  .canvas {
    position: relative;
    width: 1200px;
    height: 686px;
  }
  .card {
    position: absolute;
    width: 510px;
    height: 290px;
    border-radius: 14px;
    overflow: hidden;
    box-shadow: 1px 2px 3px rgba(40, 25, 5, 0.55);
  }
  .card-front {
    left: 67px;
    top: 116px;
    background: var(--card-white);
  }
  .card-back {
    left: 621px;
    top: 303px;
    background: radial-gradient(ellipse 55% 60% at 50% 48%, var(--brand-green-light) 0%, var(--brand-green-mid) 55%, var(--brand-green) 100%);
  }

  .brand-front {
    position: absolute;
    left: 0;
    right: 0;
    top: 44px;
    display: flex;
    align-items: center;
    justify-content: center;
    gap: 12px;
  }
  .brand-square {
    width: 36px;
    height: 36px;
    background: var(--brand-green);
    border-radius: 3px;
    flex: none;
  }
  .brand-name {
    font-size: 34px;
    font-weight: 400;
    color: var(--brand-green);
    line-height: 1;
    white-space: nowrap;
  }

  .contact-tab {
    position: absolute;
    left: 0;
    top: 131px;
  }
  .contact-list {
    position: absolute;
    left: 30px;
    top: 173px;
    margin: 0;
    padding: 0;
    list-style: none;
  }
  .contact-list li {
    display: flex;
    align-items: center;
    height: 20px;
    font-size: 12.5px;
    color: var(--text-dark);
    white-space: nowrap;
  }
  .contact-list svg {
    width: 14px;
    height: 12px;
    margin-right: 10px;
    flex: none;
  }
  .person-name {
    position: absolute;
    right: 41px;
    top: 188px;
    font-size: 19px;
    font-weight: 700;
    color: var(--name-green);
    white-space: nowrap;
  }

  .brand-back {
    position: absolute;
    inset: 0;
    display: flex;
    align-items: center;
    justify-content: center;
    gap: 14px;
  }
  .brand-back .brand-square {
    width: 40px;
    height: 40px;
    background: var(--card-white);
  }
  .brand-back .brand-name {
    color: var(--card-white);
    font-size: 36px;
  }
</style>
</head>
<body>
<main class="canvas">

  <section class="card card-front" aria-label="Business card front">
    <div class="brand-front">
      <span class="brand-square"></span>
      <span class="brand-name">Orlenby Build Co</span>
    </div>

    <svg class="contact-tab" width="56" height="134" viewBox="0 0 56 134" aria-hidden="true">
      <defs>
        <linearGradient id="tabGreen" x1="0" y1="0" x2="1" y2="0">
          <stop offset="0" stop-color="#5fae2a"/>
          <stop offset="1" stop-color="#8cc83e"/>
        </linearGradient>
      </defs>
      <polygon points="0,0 50,40 50,94 0,132" fill="url(#tabGreen)" stroke="#4a8f1f" stroke-width="1"/>
    </svg>

    <ul class="contact-list">
      <li>
        <svg viewBox="0 0 14 12" aria-hidden="true"><path d="M1.5 6.5 C3 2 11 2 12.5 6.5 L10.5 8 L9.5 6.2 C8 5.6 6 5.6 4.5 6.2 L3.5 8 Z" fill="#fff"/></svg>
        123-456-7890
      </li>
      <li>
        <svg viewBox="0 0 14 12" aria-hidden="true"><rect x="4" y="0.5" width="6" height="4" fill="none" stroke="#fff"/><rect x="1" y="4.5" width="12" height="5" fill="#fff"/><rect x="4" y="8" width="6" height="3.5" fill="#fff" stroke="#8cc83e" stroke-width="0.8"/></svg>
        123-456-7890
      </li>
      <li>
        <svg viewBox="0 0 14 12" aria-hidden="true"><rect x="1.5" y="2.5" width="11" height="7.5" fill="#fff"/><path d="M1.5 2.5 L7 7 L12.5 2.5" fill="none" stroke="#8cc83e" stroke-width="1"/></svg>
        name@website.com
      </li>
    </ul>

    <div class="person-name">Your Name</div>
  </section>

  <section class="card card-back" aria-label="Business card back">
    <div class="brand-back">
      <span class="brand-square"></span>
      <span class="brand-name">Orlenby Build Co</span>
    </div>
  </section>

</main>
</body>
</html>
```